RW Framewell Inc Business cards

We need business cards using our existing logo but slightly modified. Right now the logo says RW Loadbearing Masonry. We want to keep the RW part of the design, but replace the Structural Concrete portion with "FRAMEWELL". Please see the attached file.
Ideally this would be a blank template so we can add Different Names, titles, and phone numbers later.
On the one side we want only the logo and on the other side the detail. I'm attaching an example for you to see.
Please reach out with any other questions. Our address and other details will be given out once we find a design we like.

Target Market(s)

Construction Industry

```html
<!DOCTYPE html>
<html lang="en">
<head>
<meta charset="utf-8">
<title>RW Framewell Inc – Business Cards</title>
<link rel="stylesheet" href="https://fonts.googleapis.com/css2?family=Montserrat:wght@600&family=Roboto:wght@400;500&display=swap">
<style>
  :root {
    --bg: #5a80b6;
    --brand-blue: #2f62a6;
    --brand-blue-deep: #245391;
    --accent-blue: #2e63b0;
    --card-white: #f3f3f1;
    --ink-grey: #6d6d6d;
    --mark-grey: #6f6f6f;
  }
  * { box-sizing: border-box; margin: 0; padding: 0; }
  html, body {
    width: 1200px;
    height: 852px;
    overflow: hidden;
    background: var(--bg);
  }
  .canvas {
    position: relative;
    width: 1200px;
    height: 852px;
  }
  .card {
    position: absolute;
    top: 272px;
    width: 540px;
    height: 308px;
    border-radius: 28px;
    overflow: hidden;
    box-shadow: 0 6px 14px rgba(20, 40, 80, 0.35);
  }
  .card--back {
    left: 40px;
    background: var(--brand-blue);
    display: flex;
    align-items: center;
    justify-content: center;
  }
  .card--front {
    left: 620px;
    background: var(--card-white);
  }
  .wordmark {
    font-family: "Montserrat", sans-serif;
    font-weight: 600;
    letter-spacing: 4px;
    white-space: nowrap;
  }
  .card--back .wordmark {
    font-size: 40px;
    color: var(--brand-blue-deep);
  }
  .front-logo {
    position: absolute;
    right: 36px;
    top: 118px;
    display: flex;
    align-items: center;
    gap: 10px;
  }
  .front-logo .mark-square {
    width: 14px;
    height: 14px;
    background: var(--mark-grey);
  }
  .front-logo .wordmark {
    font-size: 26px;
    color: var(--accent-blue);
    letter-spacing: 3px;
  }
  .edge-tab {
    position: absolute;
    left: -16px;
    top: 78px;
    width: 32px;
    height: 32px;
    border-radius: 50%;
    background: var(--accent-blue);
  }
  .identity {
    position: absolute;
    left: 34px;
    top: 76px;
  }
  .identity .person-name {
    font-family: "Montserrat", sans-serif;
    font-weight: 600;
    font-size: 19px;
    color: var(--accent-blue);
  }
  .identity .person-title {
    font-family: "Roboto", sans-serif;
    font-size: 13px;
    color: var(--ink-grey);
    margin-top: 2px;
  }
  .details {
    position: absolute;
    left: 34px;
    top: 176px;
    font-family: "Roboto", sans-serif;
    font-size: 13px;
    color: var(--ink-grey);
    line-height: 1.45;
  }
  .details .divider {
    width: 226px;
    height: 1.5px;
    background: var(--accent-blue);
    margin: 6px 0 8px;
  }
  .contact-line {
    display: flex;
    align-items: center;
    gap: 10px;
  }
  .contact-line svg {
    width: 12px;
    height: 12px;
    fill: var(--accent-blue);
    flex: none;
  }
</style>
</head>
<body>
<main class="canvas">

  <section class="card card--back" aria-label="Card back with logo">
    <span class="wordmark">RW FRAMEWELL</span>
  </section>

  <section class="card card--front" aria-label="Card front with contact details">
    <span class="edge-tab"></span>

    <div class="identity">
      <p class="person-name">Evan RW Hale</p>
      <p class="person-title">Managing Director</p>
    </div>

    <div class="details">
      <p>58 Beamline Rd., Oak Vale,<br>California, US 902104</p>
      <div class="divider"></div>
      <p class="contact-line">
        <svg viewBox="0 0 24 24" aria-hidden="true"><path d="M6.6 10.8a15.1 15.1 0 0 0 6.6 6.6l2.2-2.2c.3-.3.7-.4 1-.2 1.1.4 2.3.6 3.6.6.6 0 1 .4 1 1V20c0 .6-.4 1-1 1A17 17 0 0 1 3 4c0-.6.4-1 1-1h3.5c.6 0 1 .4 1 1 0 1.3.2 2.5.6 3.6.1.3 0 .7-.2 1z"/></svg>
        555-014-2290
      </p>
      <p class="contact-line">
        <svg viewBox="0 0 24 24" aria-hidden="true"><path d="M2 5h20v14H2zm2 2v.5l8 5 8-5V7l-8 5z"/></svg>
        evan@framewellco.com
      </p>
      <p class="contact-line">
        <svg viewBox="0 0 24 24" aria-hidden="true"><path d="M12 2a10 10 0 1 0 0 20 10 10 0 0 0 0-20zm6.9 6h-3a15 15 0 0 0-1.3-3.9A8 8 0 0 1 18.9 8zM12 4c.8 1.2 1.5 2.5 1.9 4h-3.8c.4-1.5 1.1-2.8 1.9-4zM4.3 14a8 8 0 0 1 0-4h3.4a16 16 0 0 0 0 4zm.8 2h3a15 15 0 0 0 1.3 3.9A8 8 0 0 1 5.1 16zm3-8h-3a8 8 0 0 1 4.3-3.9A15 15 0 0 0 8.1 8zM12 20c-.8-1.2-1.5-2.5-1.9-4h3.8c-.4 1.5-1.1 2.8-1.9 4zm2.3-6H9.7a14 14 0 0 1 0-4h4.6a14 14 0 0 1 0 4zm.3 5.9a15 15 0 0 0 1.3-3.9h3a8 8 0 0 1-4.3 3.9zm1.7-5.9a16 16 0 0 0 0-4h3.4a8 8 0 0 1 0 4z"/></svg>
        www.framewellco.com
      </p>
    </div>

    <div class="front-logo">
      <span class="mark-square"></span>
      <span class="wordmark">RW FRAMEWELL</span>
    </div>
  </section>

</main>
</body>
</html>
```